Business Card Design Project : Ridgeline Press

In preparation for market launch, Tamarind's Ridgeline Press require the development of a business card. Ridgeline Press is a Community online publishing web portal. We provide the the city of Whistler located in B.C. (Canada) business directories, News, Classified ads, News, Events and blogs etc.

The main focus of the brand is to help local businesses to corporate with their online advertisement and marketing. Meeting our clients face to face is a must (B2B).

Target Market(s)

The target market is B2B customers. Business Owners to Marketing, advertising Managers

Industry/Entity Type

Business

Requirements
Must have
• - The business card will be two sided.
the BACK side will have our logo which consist of (icon, url,slogan) submited. The logo will be middle and centred.

The FRONT side should have company details:

Company Legal Name: TAMARIND RIDGELINE MEDIA

Owen Farsk
Director of Sales & Marketing

www.tamarindridgeline.biz
owen@tamarindridgeline.biz

Phone: 604 317 8842
#2714 - 582 E. Halvern St.
Vancouver, B.C. V7K2R4 Canada
Nice to have
• - For the "FRONT" side of our business card. You can separate or re-arrange with our logo components (icon, logo,slogan). It does not have to be together.

Also our company legal name is rather long so arrange or organize the name in a way to make it shorter. Your experience and creativity will have to come in play.
Should not have
• should not have other colors beside logo color and black text (2 colors). Also nothing Three dimensional

```html
<!DOCTYPE html>
<html lang="en">
<head>
<meta charset="utf-8">
<title>Ridgeline Press – Business Card</title>
<link href="https://fonts.googleapis.com/css2?family=Open+Sans:wght@400;700;800&family=Arimo:wght@400;700&display=swap" rel="stylesheet">
<style>
  :root {
    --brand-blue: #1572bd;
    --brand-blue-deep: #0b5a9c;
    --brand-blue-light: #2d8ad0;
    --ink: #1a1a1a;
    --text-grey: #333333;
    --rule-grey: #c9c9c9;
    --card-white: #ffffff;
    --backdrop: #e6e8ea;
  }
  * { box-sizing: border-box; margin: 0; padding: 0; }
  html, body {
    width: 1200px; height: 944px; overflow: hidden;
    background: var(--backdrop);
  }
  .canvas { position: relative; width: 1200px; height: 944px; }

  .card {
    position: absolute;
    width: 640px; height: 366px;
    border-radius: 26px;
    overflow: hidden;
  }

  /* Back side */
  .card--back {
    left: 80px; top: 90px;
    background: linear-gradient(180deg, var(--brand-blue-light) 0%, var(--brand-blue) 45%, var(--brand-blue-deep) 100%);
    display: flex; flex-direction: column; align-items: center; justify-content: center;
    text-align: center;
  }
  .brand-name {
    display: flex; align-items: center; gap: 14px;
    font-family: "Open Sans", sans-serif; font-weight: 700;
  }
  .brand-name__dot { width: 22px; height: 22px; border-radius: 50%; background: currentColor; }
  .card--back .brand-name { color: var(--card-white); font-size: 46px; margin-bottom: 28px; }
  .back-url {
    font-family: "Open Sans", sans-serif; font-weight: 800;
    font-size: 38px; color: var(--ink); letter-spacing: -0.3px; line-height: 1.1;
  }
  .back-slogan {
    font-family: "Open Sans", sans-serif; font-weight: 400;
    font-size: 29px; color: var(--card-white); margin-top: 2px;
  }

  /* Front side */
  .card--front {
    left: 480px; top: 490px;
    background: var(--card-white);
    box-shadow: 0 2px 10px rgba(0,0,0,0.12);
  }
  .front-logo {
    position: absolute; left: 34px; top: 120px; width: 230px;
    color: var(--brand-blue);
  }
  .front-logo .brand-name { font-size: 30px; gap: 10px; }
  .front-logo .brand-name__dot { width: 14px; height: 14px; }
  .front-divider {
    position: absolute; left: 282px; top: 56px; width: 1px; height: 210px;
    background: var(--rule-grey);
  }
  .contact { position: absolute; left: 304px; top: 62px; font-family: "Arimo", sans-serif; }
  .contact__name { font-size: 21px; color: var(--ink); }
  .contact__title { font-size: 14px; color: var(--brand-blue); margin-top: 3px; }
  .contact__list { list-style: none; margin-top: 36px; }
  .contact__item {
    display: flex; align-items: flex-start; gap: 8px;
    font-size: 14px; line-height: 18px; color: var(--text-grey);
    margin-bottom: 4px;
  }
  .contact__item--address { margin-bottom: 14px; }
  .contact__icon { width: 14px; height: 14px; flex: none; margin-top: 2px; fill: var(--brand-blue-deep); }
  .front-rule {
    position: absolute; left: 0; right: 0; bottom: 60px; height: 2px;
    background: var(--rule-grey);
  }
  .front-band {
    position: absolute; left: 0; right: 0; bottom: 0; height: 52px;
    background: var(--brand-blue);
    display: flex; align-items: center; padding-left: 150px;
    font-family: "Open Sans", sans-serif; font-size: 17px; color: var(--card-white);
  }
</style>
</head>
<body>
<main class="canvas">

  <section class="card card--back" aria-label="Business card back">
    <div class="brand-name"><span class="brand-name__dot"></span><span>Ridgeline Press</span></div>
    <p class="back-url">www.tamarindridgeline.biz</p>
    <p class="back-slogan">Your information gateway</p>
  </section>

  <section class="card card--front" aria-label="Business card front">
    <div class="front-logo">
      <div class="brand-name"><span class="brand-name__dot"></span><span>Ridgeline Press</span></div>
    </div>
    <div class="front-divider"></div>

    <div class="contact">
      <p class="contact__name">Owen Farsk</p>
      <p class="contact__title">Director of Sales &amp; Marketing</p>
      <ul class="contact__list">
        <li class="contact__item contact__item--address">
          <svg class="contact__icon" viewBox="0 0 14 14"><path d="M7 1 L13 7 H11 V13 H8.5 V9 H5.5 V13 H3 V7 H1 Z"/></svg>
          <span>#2714 - 582 E. Halvern St.<br>Vancouver, B.C. V7K2R4 Canada</span>
        </li>
        <li class="contact__item">
          <svg class="contact__icon" viewBox="0 0 14 14"><path d="M3 1 L5.5 1 L6.5 4.5 L5 5.6 C5.8 7.4 6.6 8.2 8.4 9 L9.5 7.5 L13 8.5 L13 11 C13 12.2 12 13 10.8 12.9 C5.6 12.4 1.6 8.4 1.1 3.2 C1 2 1.8 1 3 1 Z"/></svg>
          <span>604 317 8842</span>
        </li>
        <li class="contact__item">
          <svg class="contact__icon" viewBox="0 0 14 14"><path d="M1 3 H13 V11 H1 Z M1.6 3.6 L7 8 L12.4 3.6" fill="none" stroke="var(--brand-blue-deep)" stroke-width="1.4"/></svg>
          <span>owen@tamarindridgeline.biz</span>
        </li>
        <li class="contact__item">
          <svg class="contact__icon" viewBox="0 0 14 14"><circle cx="7" cy="7" r="6"/></svg>
          <span>www.tamarindridgeline.biz</span>
        </li>
      </ul>
    </div>

    <div class="front-rule"></div>
    <div class="front-band">Your information gateway</div>
  </section>

</main>
</body>
</html>
```